Nona's Brivelo

I am looking to design a label to be used on a glass jar for packaging a very special spice that has been used in our family for generations. The spice is excellent on meats, burgers, poultry, fish, and more.

The name of the spice is "Nona's Famous Brivelo"

Design should be traditional, with an Italian feel.

Total circumference of the jar is 10"
Height of jar is 4"

Some of the glass should not be covered to reveal color of spice inside.

Target Market(s)

Female 25-75

```html
<!DOCTYPE html>
<html lang="en">
<head>
<meta charset="utf-8">
<title>Nona's Famous Brivelo – Jar Label</title>
<link rel="stylesheet" href="https://fonts.googleapis.com/css2?family=Gelasio:wght@700&family=Playfair+Display:ital,wght@1,900&family=Arimo:wght@400&display=swap">
<style>
  :root {
    --ink: #0b0b0b;
    --accent-red: #e01515;
    --flag-red: #d0282f;
    --band-green-light: #e4efe4;
    --band-green: #a9cbab;
    --rim-white: #ffffff;
    --oval-green: #34c035;
    --oval-green-dark: #1e7c24;
    --ribbon-light: #6fb27a;
    --ribbon-dark: #1b5a2c;
    --photo-dark: #1f3b22;
    --photo-mid: #4f7c4e;
    --label-text: #ffffff;
  }
  html, body {
    margin: 0;
    padding: 0;
    width: 1200px;
    height: 810px;
    overflow: hidden;
    background: #ffffff;
  }
  .label {
    display: block;
    width: 1200px;
    height: 810px;
  }
  .brand-name {
    font-family: "Gelasio", Georgia, serif;
    font-weight: 700;
    font-size: 74px;
    fill: var(--label-text);
    stroke: var(--ink);
    stroke-width: 2.5px;
    paint-order: stroke;
  }
  .flag-word {
    font-family: "Playfair Display", Georgia, serif;
    font-style: italic;
    font-weight: 900;
    font-size: 56px;
    fill: var(--label-text);
  }
  .product-type {
    font-family: "Gelasio", Georgia, serif;
    font-weight: 700;
    font-size: 58px;
    font-variant: small-caps;
    letter-spacing: 1px;
    fill: var(--label-text);
    stroke: #184d1c;
    stroke-width: 3px;
    paint-order: stroke;
  }
  .usage-line {
    font-family: "Arimo", Arial, sans-serif;
    font-size: 29px;
    fill: var(--label-text);
  }
  .net-weight {
    font-family: "Arimo", Arial, sans-serif;
    font-size: 25px;
    fill: var(--label-text);
  }
</style>
</head>
<body>
<svg class="label" viewBox="0 0 1200 810" xmlns="http://www.w3.org/2000/svg">
  <defs>
    <radialGradient id="band-fill" cx="50%" cy="45%" r="70%">
      <stop offset="0%" stop-color="var(--band-green-light)"/>
      <stop offset="100%" stop-color="var(--band-green)"/>
    </radialGradient>
    <linearGradient id="oval-fill" x1="0" y1="0" x2="0" y2="1">
      <stop offset="0%" stop-color="#ffffff"/>
      <stop offset="45%" stop-color="#cfe8cf"/>
      <stop offset="85%" stop-color="var(--oval-green)"/>
      <stop offset="100%" stop-color="var(--oval-green-dark)"/>
    </linearGradient>
    <radialGradient id="photo-fill" cx="50%" cy="55%" r="60%">
      <stop offset="0%" stop-color="var(--photo-mid)"/>
      <stop offset="100%" stop-color="var(--photo-dark)"/>
    </radialGradient>
    <linearGradient id="ribbon-fill" x1="0" y1="0" x2="1" y2="0">
      <stop offset="0%" stop-color="var(--ribbon-dark)"/>
      <stop offset="18%" stop-color="var(--ribbon-light)"/>
      <stop offset="40%" stop-color="var(--ribbon-dark)"/>
      <stop offset="62%" stop-color="var(--ribbon-light)"/>
      <stop offset="85%" stop-color="#2e7a3d"/>
      <stop offset="100%" stop-color="var(--ribbon-dark)"/>
    </linearGradient>
    <path id="seasoning-arc" d="M375 420 A225 300 0 0 0 825 420"/>
    <path id="usage-arc" d="M305 440 A295 355 0 0 0 895 440"/>
  </defs>

  <g class="wrap-band">
    <rect x="0" y="90" width="1200" height="22" fill="var(--ink)"/>
    <rect x="0" y="112" width="1200" height="12" fill="var(--accent-red)"/>
    <rect x="0" y="124" width="1200" height="535" fill="url(#band-fill)"/>
    <rect x="0" y="659" width="1200" height="12" fill="var(--accent-red)"/>
    <rect x="0" y="671" width="1200" height="28" fill="var(--ink)"/>
  </g>

  <g class="badge">
    <ellipse cx="600" cy="420" rx="312" ry="385" fill="var(--ink)"/>
    <ellipse cx="600" cy="388" rx="292" ry="364" fill="var(--rim-white)"/>
    <ellipse cx="600" cy="390" rx="278" ry="350" fill="url(#oval-fill)"/>
    <ellipse cx="600" cy="390" rx="266" ry="338" fill="none" stroke="var(--ink)" stroke-width="2"/>
    <ellipse cx="600" cy="345" rx="180" ry="228" fill="url(#photo-fill)" stroke="#e8f3e8" stroke-width="3"
             role="img" aria-label="Photo of a fresh green herb sprig"/>
  </g>

  <g class="flag">
    <path d="M522 52 Q665 38 816 10 L806 122 Q668 134 522 150 Z" fill="var(--flag-red)" stroke="#ffffff" stroke-width="3"/>
    <text class="flag-word" x="666" y="114" text-anchor="middle" transform="rotate(-5 666 95)">Famous</text>
  </g>

  <g class="ribbon">
    <path d="M268 240 L300 232 L305 338 L275 330 Z" fill="var(--ribbon-dark)"/>
    <path d="M900 150 L935 160 L930 258 L908 255 Z" fill="var(--ribbon-dark)"/>
    <path d="M300 232 Q600 175 905 148 L910 255 Q610 272 305 338 Z" fill="url(#ribbon-fill)"/>
    <text class="brand-name" x="604" y="285" text-anchor="middle" transform="rotate(-9 604 262)">Nona's Brivelo</text>
  </g>

  <text class="product-type"><textPath href="#seasoning-arc" startOffset="50%" text-anchor="middle">Special Seasoning</textPath></text>

  <g class="net-weight-tag">
    <rect x="496" y="584" width="212" height="42" rx="21" fill="var(--ink)"/>
    <text class="net-weight" x="602" y="614" text-anchor="middle">Net Wt. 1.75 oz</text>
  </g>

  <text class="usage-line"><textPath href="#usage-arc" startOffset="50%" text-anchor="middle">Excellent on meats, burgers, poultry, fish, and more</textPath></text>
</svg>
</body>
</html>
```